Interval Timer App

Need to have design for the attached wireframe. Similar app can be found here: https://shop.lumaverse.net/store/apps/details?id=cc.quillfern.pulseclock

```html
<!DOCTYPE html>
<html lang="en">
<head>
<meta charset="UTF-8">
<title>Interval Timer</title>
<link rel="stylesheet" href="https://fonts.googleapis.com/css2?family=Open+Sans:wght@300;400;600&display=swap">
<style>
  :root {
    --bg: #ffffff;
    --brand: #1a7fe3;
    --ink: #1f2230;
    --ink-soft: #2a2d38;
    --on-brand: #ffffff;
  }
  * { box-sizing: border-box; margin: 0; padding: 0; }
  html, body {
    width: 675px;
    height: 1200px;
    overflow: hidden;
    background: var(--bg);
    font-family: "Open Sans", Arial, sans-serif;
  }
  .screen {
    position: relative;
    width: 675px;
    height: 1200px;
    background: var(--bg);
  }
  .settings-button {
    position: absolute;
    top: 38px;
    left: 589px;
    width: 56px;
    height: 56px;
    background: none;
    border: 0;
  }
  .settings-button svg { width: 56px; height: 56px; display: block; }
  .sets-label {
    position: absolute;
    top: 534px;
    left: 0;
    width: 675px;
    text-align: center;
    font-size: 38px;
    font-weight: 600;
    color: var(--ink);
    line-height: 54px;
  }
  .stepper {
    position: absolute;
    top: 621px;
    left: 202px;
    width: 272px;
    height: 45px;
  }
  .stepper-button {
    position: absolute;
    top: 0;
    width: 65px;
    height: 45px;
    background: var(--brand);
    border: 0;
    display: flex;
    align-items: center;
    justify-content: center;
  }
  .stepper-button svg { width: 26px; height: 26px; display: block; }
  .stepper-button.decrease { left: 0; border-radius: 23px 0 0 23px; }
  .stepper-button.increase { right: 0; border-radius: 0 23px 23px 0; }
  .stepper-value {
    position: absolute;
    left: 65px;
    width: 142px;
    top: 0;
    height: 45px;
    line-height: 45px;
    text-align: center;
    font-size: 42px;
    font-weight: 300;
    color: var(--ink-soft);
  }
  .start-button {
    position: absolute;
    top: 1069px;
    left: 216px;
    width: 243px;
    height: 75px;
    border-radius: 38px;
    border: 0;
    background: var(--brand);
    color: var(--on-brand);
    font-family: "Open Sans", Arial, sans-serif;
    font-size: 25px;
    font-weight: 400;
    letter-spacing: 1.5px;
  }
</style>
</head>
<body>
<main class="screen">
  <button class="settings-button" aria-label="Settings">
    <svg viewBox="0 0 24 24" fill="none" stroke="#1a7fe3" stroke-width="1" stroke-linejoin="round">
      <circle cx="12" cy="12" r="3.2"/>
      <path d="M10.3 2.5h3.4l.5 2.6 1.6.9 2.5-.9 1.7 2.9-2 1.7v1.9l2 1.7-1.7 2.9-2.5-.9-1.6.9-.5 2.6h-3.4l-.5-2.6-1.6-.9-2.5.9-1.7-2.9 2-1.7v-1.9l-2-1.7 1.7-2.9 2.5.9 1.6-.9z"/>
    </svg>
  </button>

  <h1 class="sets-label">Sets</h1>

  <div class="stepper">
    <button class="stepper-button decrease" aria-label="Decrease sets">
      <svg viewBox="0 0 26 26"><rect x="3" y="11.5" width="20" height="3" fill="#ffffff"/></svg>
    </button>
    <span class="stepper-value">3</span>
    <button class="stepper-button increase" aria-label="Increase sets">
      <svg viewBox="0 0 26 26"><rect x="3" y="11.5" width="20" height="3" fill="#ffffff"/><rect x="11.5" y="3" width="3" height="20" fill="#ffffff"/></svg>
    </button>
  </div>

  <button class="start-button">START</button>
</main>
</body>
</html>
```